Shine Fox Auto Care Business Card

2 side business card design for an auto detailing business

Target Market(s)

Auto detailing

Contact Information for Business Card

Things included

The business name “Shine Fox Auto Care”
Mark Dunrow
(403)271-6094
Battleford, Sk

Services offered - complete interior& exterior detail
- paint correction & protection
- ceramic coating
- trim restore
- auto carpet & seat cleaning

Requirements
Must have
• Colours that are in my logo

Services offered

My name Mark Dunrow
403-271-6094
Battleford, Sk

Not too sure in what order for these ?
Website. Shinefoxautocare.com
Instagram Shinefoxautocare
Email. Shinefoxautoac@mailvento.com

```html
<!DOCTYPE html>
<html lang="en">
<head>
<meta charset="utf-8">
<title>Shine Fox Auto Care – Business Card</title>
<link rel="stylesheet" href="https://fonts.googleapis.com/css2?family=Michroma&family=Arimo:wght@400;700&display=swap">
<style>
  :root {
    --backdrop: #141414;
    --card-light: #e6e6e4;
    --card-dark: #232325;
    --brand-red: #a50d10;
    --ink: #1c1c1c;
    --ink-soft: #3a3a3a;
    --rule: #b9b9b6;
    --paper-text: #f2f2f2;
    --muted-text: #9a9a9c;
    --watermark: #2e2e31;
  }
  * { box-sizing: border-box; margin: 0; padding: 0; }
  html, body { width: 1200px; height: 820px; overflow: hidden; background: var(--backdrop); }
  .canvas {
    width: 1200px; height: 820px;
    display: flex; align-items: center; justify-content: center; gap: 36px;
  }
  .card {
    position: relative; width: 560px; height: 320px; overflow: hidden;
    border-bottom: 4px solid var(--brand-red);
    border-left: 2px solid var(--brand-red);
  }

  /* Front */
  .card-front { background: var(--card-light); font-family: "Arimo", Arial, sans-serif; color: var(--ink-soft); }
  .brand { position: absolute; top: 42px; left: 260px; width: 260px; text-align: center; }
  .brand-dot {
    width: 58px; height: 58px; margin: 0 auto 16px;
    border: 7px solid var(--brand-red); border-radius: 50%;
  }
  .brand-name {
    font-family: "Michroma", sans-serif; font-size: 17px; line-height: 1.35;
    letter-spacing: 1px; color: var(--ink);
  }
  .divider { position: absolute; left: 196px; right: 30px; top: 196px; height: 1px; background: var(--rule); }
  .holder-name {
    position: absolute; left: 30px; top: 182px;
    font-family: "Michroma", sans-serif; font-size: 19px; color: var(--brand-red); letter-spacing: 0.5px;
  }
  .contact-list { position: absolute; left: 30px; top: 224px; list-style: none; }
  .contact-list li { display: flex; align-items: center; gap: 9px; font-size: 14px; margin-bottom: 6px; }
  .icon-badge {
    width: 20px; height: 20px; border-radius: 50%; background: var(--brand-red);
    display: flex; align-items: center; justify-content: center; flex: none;
  }
  .social-list { position: absolute; right: 30px; top: 222px; list-style: none; text-align: right; }
  .social-list li { display: flex; align-items: center; justify-content: flex-end; gap: 9px; font-size: 14px; margin-bottom: 8px; }
  .plain-badge { width: 20px; height: 20px; border-radius: 50%; background: var(--brand-red); flex: none; }

  /* Back */
  .card-back { background: var(--card-dark); font-family: "Arimo", Arial, sans-serif; }
  .watermark-ring {
    position: absolute; left: 20px; top: 30px; width: 270px; height: 270px;
    border: 34px solid var(--watermark); border-radius: 50%;
  }
  .services { position: absolute; left: 300px; top: 58px; width: 240px; }
  .services-title { font-weight: 700; font-size: 17px; color: var(--paper-text); letter-spacing: 0.3px; }
  .services-lead { margin-top: 8px; font-size: 13px; line-height: 1.3; color: var(--muted-text); text-transform: uppercase; }
  .services-list { list-style: none; margin-top: 20px; }
  .services-list li {
    position: relative; padding-left: 14px; margin-bottom: 7px;
    font-size: 12px; color: var(--paper-text); text-transform: uppercase;
  }
  .services-list li::before {
    content: ""; position: absolute; left: 0; top: 4px;
    width: 7px; height: 7px; border-radius: 50%; background: var(--brand-red);
  }
</style>
</head>
<body>
<main class="canvas">

  <section class="card card-front" aria-label="Business card front">
    <div class="brand">
      <div class="brand-dot"></div>
      <p class="brand-name">SHINE FOX<br>AUTO CARE</p>
    </div>
    <div class="divider"></div>
    <h1 class="holder-name">MARK DUNROW</h1>
    <ul class="contact-list">
      <li><span class="icon-badge"><svg width="11" height="11" viewBox="0 0 24 24"><path fill="#fff" d="M6.6 10.8a15 15 0 0 0 6.6 6.6l2.2-2.2c.3-.3.7-.4 1-.2 1.1.4 2.3.6 3.6.6.6 0 1 .4 1 1V20c0 .6-.4 1-1 1A17 17 0 0 1 3 4c0-.6.4-1 1-1h3.5c.6 0 1 .4 1 1 0 1.3.2 2.5.6 3.6.1.3 0 .7-.2 1z"/></svg></span>(403)271-6094</li>
      <li><span class="icon-badge"><svg width="11" height="11" viewBox="0 0 24 24"><rect x="2" y="5" width="20" height="14" rx="1" fill="#fff"/><path d="M2 6l10 7 10-7" stroke="#a50d10" stroke-width="2" fill="none"/></svg></span>shinefoxac@mailvento.com</li>
      <li><span class="icon-badge"><svg width="12" height="12" viewBox="0 0 24 24" fill="none" stroke="#fff" stroke-width="2"><circle cx="12" cy="12" r="9"/><path d="M3 12h18M12 3c3 3 3 15 0 18M12 3c-3 3-3 15 0 18"/></svg></span>www.Shinefoxautocare.com</li>
    </ul>
    <ul class="social-list">
      <li>Shinefoxautocare<span class="plain-badge"></span></li>
      <li>Battleford, Sk<span class="icon-badge"><svg width="11" height="11" viewBox="0 0 24 24"><path fill="#fff" d="M12 2a7 7 0 0 0-7 7c0 5 7 13 7 13s7-8 7-13a7 7 0 0 0-7-7zm0 9.5A2.5 2.5 0 1 1 12 6.5a2.5 2.5 0 0 1 0 5z"/></svg></span></li>
    </ul>
  </section>

  <section class="card card-back" aria-label="Business card back">
    <div class="watermark-ring"></div>
    <div class="services">
      <h2 class="services-title">SERVICES OFFERED</h2>
      <p class="services-lead">Complete interior &amp;<br>exterior detail</p>
      <ul class="services-list">
        <li>Ceramic coating</li>
        <li>Trim restore</li>
        <li>Paint correction &amp; protection</li>
        <li>Auto carpet &amp; seat cleaning</li>
      </ul>
    </div>
  </section>

</main>
</body>
</html>
```